Business card design for my company.
I would like the card's background colour to be black. You can also see our web site to get an idea of our brand. https://www.tmwhomecrafting.com.au/
- Name
- Email

```html
<!DOCTYPE html>
<html lang="en">
<head>
<meta charset="utf-8">
<title>TMW Home Crafting – Business Card</title>
<link href="https://fonts.googleapis.com/css2?family=Open+Sans:wght@400;600&family=Montserrat:wght@700&display=swap" rel="stylesheet">
<style>
  :root {
    --stage: #2b2c2e;
    --card: #1c1c1c;
    --green: #16a03f;
    --white: #ffffff;
    --text-soft: #e6e6e6;
  }
  html, body {
    margin: 0;
    padding: 0;
    width: 1200px;
    height: 1088px;
    overflow: hidden;
    background: var(--stage);
  }
  .stage {
    position: relative;
    width: 1200px;
    height: 1088px;
  }
  .card {
    position: absolute;
    left: 220px;
    width: 760px;
    height: 434px;
    background: var(--card);
    overflow: hidden;
    box-shadow: 0 18px 40px rgba(0,0,0,.45);
    font-family: "Open Sans", sans-serif;
    color: var(--text-soft);
  }
  .card--front { top: 80px; }
  .card--back { top: 574px; }

  /* Front */
  .brand {
    position: absolute;
    right: 52px;
    top: 70px;
    display: flex;
    align-items: center;
    gap: 16px;
  }
  .brand__square {
    width: 26px;
    height: 26px;
    background: var(--green);
  }
  .brand__name {
    font-family: "Montserrat", sans-serif;
    font-weight: 700;
    font-size: 34px;
    letter-spacing: 4px;
    color: var(--white);
    line-height: 1.15;
    text-align: right;
  }
  .person {
    position: absolute;
    left: 56px;
    top: 196px;
  }
  .person__name {
    margin: 0;
    font-weight: 600;
    font-size: 22px;
    letter-spacing: .5px;
    color: var(--green);
    text-transform: uppercase;
  }
  .person__title {
    margin: 2px 0 0;
    font-size: 17px;
    color: var(--text-soft);
  }
  .rule {
    position: absolute;
    left: 56px;
    right: 52px;
    top: 262px;
    height: 1px;
    background: var(--white);
  }
  .address {
    position: absolute;
    right: 52px;
    top: 276px;
    margin: 0;
    font-size: 15px;
    line-height: 1.4;
    text-align: right;
    font-style: normal;
  }
  .contact {
    position: absolute;
    left: 56px;
    top: 284px;
    margin: 0;
    padding: 0;
    list-style: none;
    font-size: 16px;
  }
  .contact li {
    display: flex;
    align-items: center;
    gap: 10px;
    margin-bottom: 8px;
  }
  .contact svg { width: 14px; height: 14px; fill: var(--green); }
  .footer-band {
    position: absolute;
    left: 0;
    bottom: 0;
    width: 760px;
    height: 64px;
  }
  .website {
    position: absolute;
    right: 40px;
    bottom: 14px;
    font-size: 16px;
    color: var(--white);
  }

  /* Back */
  .back-mark {
    position: absolute;
    inset: 0;
    display: flex;
    align-items: center;
    justify-content: center;
    gap: 20px;
  }
  .back-mark__square {
    width: 34px;
    height: 34px;
    background: var(--white);
  }
  .back-mark__name {
    font-family: "Montserrat", sans-serif;
    font-weight: 700;
    font-size: 46px;
    letter-spacing: 8px;
    color: var(--white);
  }
</style>
</head>
<body>
<main class="stage">

  <section class="card card--front" aria-label="Business card front">
    <div class="brand">
      <span class="brand__square"></span>
      <span class="brand__name">TMW<br>HOME CRAFTING</span>
    </div>

    <div class="person">
      <h1 class="person__name">Daniel Hartley</h1>
      <p class="person__title">Managing Director</p>
    </div>

    <div class="rule"></div>

    <address class="address">Riverton, Tasmania<br>Australia</address>

    <ul class="contact">
      <li>
        <svg viewBox="0 0 16 16" aria-hidden="true"><path d="M3 1h3l1.5 4-2 1.2a9 9 0 0 0 4.3 4.3L11 8.5l4 1.5v3a2 2 0 0 1-2 2A13 13 0 0 1 1 3a2 2 0 0 1 2-2z"/></svg>
        0400 123 456
      </li>
      <li>
        <svg viewBox="0 0 16 16" aria-hidden="true"><path d="M1 3h14v10H1z M1 3l7 6 7-6" fill="none" stroke="#16a03f" stroke-width="1.6"/></svg>
        info@tmwhomecrafting.com.au
      </li>
    </ul>

    <svg class="footer-band" viewBox="0 0 760 64" preserveAspectRatio="none" aria-hidden="true">
      <path d="M0 52 H440 C470 52 480 20 510 20 H760 V64 H0 Z" fill="#16a03f"/>
      <path d="M0 46 H436 C462 46 470 40 476 34 L480 34 C472 44 462 52 440 52 H0 Z" fill="#ffffff"/>
    </svg>
    <span class="website">www.tmwhomecrafting.com.au</span>
  </section>

  <section class="card card--back" aria-label="Business card back">
    <div class="back-mark">
      <span class="back-mark__square"></span>
      <span class="back-mark__name">TMW HOME CRAFTING</span>
    </div>
  </section>

</main>
</body>
</html>
```